Harlow Mechanical Contractors needs a Website

Create basic website for commercial plumbing and mechanical contractor; to include pictures of works in progress and completed works, description of all services offered and geographical locations and licenses

Target Market(s)

General Contractors, Real Estate Developers, Construction Companies

Industry/Entity Type

Construction

Coding

Coded - Design and coding required

Number of Pages Required

5+ page

• See logo attached to project

Colors
0392cd

```html
<!DOCTYPE html>
<html lang="en">
<head>
<meta charset="utf-8">
<title>Harlow Mechanical Contractors</title>
<link rel="stylesheet" href="https://fonts.googleapis.com/css2?family=Lato:wght@400;700&family=Open+Sans:wght@400;600&display=swap">
<style>
:root{
  --blue:#0392cd;
  --blue-light:#1aa3dd;
  --heading:#555555;
  --text:#666666;
  --navy:#1d3557;
  --panel:#f7f7f7;
  --footer:#6e6e6e;
  --footer-text:#e9e9e9;
  --white:#ffffff;
}
*{margin:0;padding:0;box-sizing:border-box}
html,body{width:1200px;height:2416px;overflow:hidden;background:var(--white)}
body{position:relative;font-family:"Open Sans",Arial,sans-serif;color:var(--text)}
.abs{position:absolute}
.heading{font-family:"Lato",Arial,sans-serif;font-weight:700}

/* top bar */
.topbar{left:0;top:0;width:1200px;height:42px;background:linear-gradient(#18a6e2,#0392cd)}
.topbar-contact{left:132px;top:12px;font-size:12px;color:var(--white);display:flex;align-items:center;gap:8px;font-family:"Lato",Arial,sans-serif}
.topbar-contact svg{width:11px;height:11px}
.search{left:910px;top:5px;width:156px;height:31px;background:rgba(255,255,255,.12);border:1px solid rgba(255,255,255,.25);color:var(--white);font-size:12px;padding:7px 10px}
.search svg{position:absolute;right:10px;top:9px;width:12px;height:12px}

/* header */
.header{left:0;top:42px;width:1200px;height:111px;background:var(--white);box-shadow:0 2px 4px rgba(0,0,0,.06)}
.brand{left:132px;top:62px;display:flex;align-items:center;gap:12px}
.brand-mark{width:46px;height:46px;border-radius:50%;background:var(--blue)}
.brand-name{font-family:"Lato",Arial,sans-serif;font-weight:700;font-size:15px;line-height:17px;color:var(--navy);text-transform:uppercase}
.nav{top:89px;font-family:"Lato",Arial,sans-serif;font-size:12px;letter-spacing:1px;color:#444;text-transform:uppercase}
.nav.active{color:var(--blue)}

/* hero */
.hero{left:0;top:153px;width:1200px;height:419px;background:linear-gradient(90deg,#e8e8e8 0%,#dcdcdc 38%,#a9a9a9 60%,#8d8d8d 80%,#b4b4b4 100%)}
.hero-title{left:132px;top:238px;font-size:52px;line-height:58px;color:var(--blue-light);text-transform:uppercase}
.hero-text{left:132px;top:364px;width:300px;font-size:13px;line-height:19px;color:#444}
.btn{background:linear-gradient(#1ba9e6,#0392cd);color:var(--white);text-align:center;border-radius:3px}
.hero-btn{left:134px;top:432px;width:169px;height:43px;font-family:"Lato",Arial,sans-serif;font-size:15px;line-height:43px}
.hero-arrow{left:68px;top:359px;width:33px;height:33px;border-radius:50%;background:#5d5d5d}

/* section headings */
.section-title{left:0;width:1200px;text-align:center;font-size:31px;color:var(--heading);text-transform:uppercase}
.welcome-text{left:180px;top:660px;width:840px;text-align:center;font-size:12px;line-height:20px}
.welcome-btn{left:556px;top:744px;width:88px;height:34px;font-size:12px;line-height:34px}

/* services */
.services{left:0;top:831px;width:1200px;height:409px;background:var(--panel);border-top:1px solid #e6e6e6}
.service{top:950px;width:320px;text-align:center}
.service svg{display:block;margin:0 auto;height:90px}
.service-title{margin-top:34px;font-size:20px;color:var(--blue);text-transform:uppercase}
.service-text{margin:12px auto 0;width:260px;font-size:12px;line-height:19px}
.read-more{display:inline-block;margin-top:14px;font-size:11px;color:var(--blue);text-decoration:underline;text-transform:uppercase}

/* testimonials */
.testimonials{left:0;top:1240px;width:1200px;height:287px;background:linear-gradient(90deg,#4a4f57 0%,#6a6c70 40%,#8a8a8a 70%,#7a7a7a 100%)}
.avatar{left:132px;top:1334px;width:120px;height:120px;border-radius:50%;background:#b79a86;border:4px solid var(--white)}
.quote{left:282px;top:1364px;width:790px;font-size:12px;line-height:20px;color:var(--white)}
.quote-name{left:286px;top:1418px;font-size:12px;color:var(--blue-light)}
.dots{left:582px;top:1480px;display:flex;gap:8px}
.dots span{width:6px;height:6px;border-radius:50%;background:var(--white)}
.dots span.on{background:var(--blue)}

/* projects */
.card{top:1653px;width:290px;height:393px;border:1px solid #e3e3e3;background:var(--white)}
.card-image{height:185px}
.card-body{padding:22px 23px}
.card-title{font-size:20px;color:var(--blue);text-transform:uppercase}
.card-date{margin-top:12px;font-size:11px;font-weight:600;color:#333;display:flex;gap:7px;align-items:center}
.card-text{margin-top:18px;font-size:12px;line-height:19px}
.card .read-more{margin-top:20px;font-size:11px}

/* footer */
.footer{left:0;top:2107px;width:1200px;height:309px;background:var(--footer);color:var(--footer-text)}
.footer-brand{left:132px;top:2150px;display:flex;align-items:center;gap:12px}
.footer-brand .brand-mark{background:#9a9a9a}
.footer-brand .brand-name{color:#d6d6d6}
.social{left:132px;top:2237px;display:flex;gap:5px}
.social span{width:31px;height:31px;border-radius:50%;border:2px solid var(--white)}
.footer-heading{top:2143px;font-family:"Lato",Arial,sans-serif;font-weight:700;font-size:15px;color:var(--white);text-transform:uppercase}
.quick-links{left:406px;top:2177px;font-size:11px;line-height:21px;list-style:none;color:var(--white)}
.newsletter-note{left:615px;top:2180px;font-size:11px;color:#dedede}
.newsletter-input{left:615px;top:2215px;width:195px;height:34px;background:#999;color:var(--white);font-size:11px;padding:10px 12px}
.subscribe{left:615px;top:2270px;width:83px;height:24px;font-size:11px;line-height:24px;background:var(--blue);color:var(--white);text-align:center}
.contact-row{left:884px;font-size:11px;line-height:16px;display:flex;gap:12px;color:var(--white)}
.contact-row svg{width:12px;height:12px;flex:none;margin-top:2px}
.footer-rule{left:132px;top:2357px;width:934px;height:1px;background:#888}
.copyright{left:0;top:2379px;width:1200px;text-align:center;font-size:10px;color:var(--white)}
</style>
</head>
<body>

<div class="abs topbar"></div>
<div class="abs topbar-contact">
  <svg viewBox="0 0 12 12"><path d="M2.5 1l2 2-1 1.5a7 7 0 0 0 4 4L9 7.5l2 2-1.5 1.5C5 11 1 7 1 2.5z" fill="#fff"/></svg>
  <span>01632 960144</span><span>|</span>
  <svg viewBox="0 0 12 12"><rect x="1" y="2.5" width="10" height="7" fill="none" stroke="#fff"/><path d="M1 2.5l5 4 5-4" fill="none" stroke="#fff"/></svg>
  <span>info@harlowmech.example</span>
</div>
<div class="abs search">Search
  <svg viewBox="0 0 12 12"><circle cx="5" cy="5" r="3.5" fill="none" stroke="#fff" stroke-width="1.6"/><path d="M7.6 7.6L11 11" stroke="#fff" stroke-width="1.8"/></svg>
</div>

<header class="abs header"></header>
<div class="abs brand"><span class="brand-mark"></span><span class="brand-name">Harlow<br>Mechanical<br>Contractors</span></div>
<nav>
  <span class="abs nav active" style="left:432px">Home</span>
  <span class="abs nav" style="left:511px">About Us</span>
  <span class="abs nav" style="left:615px">Services</span>
  <span class="abs nav" style="left:715px">Projects</span>
  <span class="abs nav" style="left:818px">Gallery</span>
  <span class="abs nav" style="left:913px">News</span>
  <span class="abs nav" style="left:991px">Contact Us</span>
</nav>

<section class="abs hero" role="img" aria-label="Photo of an adjustable wrench, pipe fittings and braided hoses on a white wooden surface"></section>
<div class="abs hero-arrow"><svg viewBox="0 0 33 33" width="33" height="33"><path d="M19 10l-6 6.5 6 6.5" fill="none" stroke="#fff" stroke-width="2.5"/></svg></div>
<h1 class="abs heading hero-title">Commercial<br>Plumbing</h1>
<p class="abs hero-text">Nemo enim ipsam voluptatem quia voluptas sit asper­natur aut odit aut fugit,</p>
<div class="abs btn hero-btn">REQUEST QUOTE</div>

<h2 class="abs heading section-title" style="top:612px">Welcome to Harlow Mechanical Contractors</h2>
<p class="abs welcome-text">Nemo enim ipsam voluptatem quia voluptas sit aspernatur aut odit aut fugit, sed quia consequuntur magni dolores eos qui ratione voluptatem sequi nesciunt. Neque porro quisquam est, qui dolorem ipsum quia dolor sit amet, consectetur, adipisci velit, sed quia non numquam eius modi tempora incidunt ut labore et dolore magnam aliquam quaerat voluptatem.</p>
<div class="abs btn welcome-btn">Read More</div>

<section class="abs services"></section>
<h2 class="abs heading section-title" style="top:880px">Our Services</h2>

<div class="abs service" style="left:93px">
  <svg viewBox="0 0 90 90" width="90"><path d="M5 12h14v8h30v-8h14v8h12v10h-12v8H49v-8H33v12h8v12H23V38H19v8H5z" fill="#0392cd"/><path d="M66 58c4 7 6 10 6 13a6 6 0 0 1-12 0c0-3 2-6 6-13z" fill="#0392cd"/></svg>
  <h3 class="heading service-title">Large Offices</h3>
  <p class="service-text">Nemo enim ipsam voluptatem quia voluptas sit aspernatur aut odit aut fugit.</p>
  <span class="read-more">Read More</span>
</div>
<div class="abs service" style="left:439px">
  <svg viewBox="0 0 130 90" width="130"><path d="M10 10h60v76H10zM70 30h50v56H70z" fill="#0392cd"/><g fill="#fff"><rect x="18" y="20" width="9" height="10"/><rect x="35" y="20" width="9" height="10"/><rect x="52" y="20" width="9" height="10"/><rect x="18" y="40" width="9" height="10"/><rect x="35" y="40" width="9" height="10"/><rect x="52" y="40" width="9" height="10"/><rect x="18" y="60" width="9" height="10"/><rect x="52" y="60" width="9" height="10"/><rect x="34" y="64" width="12" height="22"/><rect x="80" y="40" width="8" height="9"/><rect x="96" y="40" width="8" height="9"/><rect x="80" y="58" width="8" height="9"/><rect x="96" y="58" width="8" height="9"/></g></svg>
  <h3 class="heading service-title">Condominiums</h3>
  <p class="service-text">Nemo enim ipsam voluptatem quia voluptas sit aspernatur aut odit aut fugit</p>
  <span class="read-more">Read More</span>
</div>
<div class="abs service" style="left:784px">
  <svg viewBox="0 0 90 90" width="90"><path d="M14 74L60 28" stroke="#0392cd" stroke-width="10" stroke-linecap="round"/><path d="M56 8a16 16 0 0 0-4 20l8 8a16 16 0 0 0 20-4l-10-2-4-6 2-10z" fill="#0392cd"/><path d="M18 14l8-4 44 52" stroke="#0392cd" stroke-width="7" fill="none"/><path d="M64 58l16 16-6 6-16-16z" fill="#0392cd"/></svg>
  <h3 class="heading service-title">Industrial Projects</h3>
  <p class="service-text">Nemo enim ipsam voluptatem quia voluptas sit aspernatur aut odit aut fugit</p>
  <span class="read-more">Read More</span>
</div>

<section class="abs testimonials" role="img" aria-label="Photo of a plumber's hand fitting a wall tap"></section>
<h2 class="abs heading section-title" style="top:1285px;color:#fff">Testimonials</h2>
<div class="abs avatar" role="img" aria-label="Customer portrait"></div>
<p class="abs quote">“Neque porro quisquam est qui dolorem ipsum quia dolor sit amet, consectetur, adipisci velit...”“There is no one who loves pain itself, who seeks after it and wants to have it, simply because it is pain...”</p>
<span class="abs quote-name">Mark Ellis</span>
<div class="abs dots"><span></span><span class="on"></span><span></span></div>

<h2 class="abs heading section-title" style="top:1568px">Recent Projects</h2>

<article class="abs card" style="left:132px">
  <div class="card-image" role="img" aria-label="Photo of a modern white bathroom with a freestanding basin" style="background:linear-gradient(90deg,#cfe0e4,#3f4d5f 45%,#e9eef2 80%)"></div>
  <div class="card-body">
    <h3 class="heading card-title">Large Offices</h3>
    <div class="card-date"><svg width="10" height="10" viewBox="0 0 10 10"><rect y="2" width="10" height="8" fill="#333"/><rect x="2" width="1.5" height="3" fill="#333"/><rect x="6.5" width="1.5" height="3" fill="#333"/></svg>26JUL, 2016</div>
    <p class="card-text">Nemo enim ipsam voluptatem quia voluptas sit aspernatur aut odit aut fugit, sed quia conse­quuntur magni dolores eos</p>
    <span class="read-more">Read More »</span>
  </div>
</article>
<article class="abs card" style="left:456px">
  <div class="card-image" role="img" aria-label="Photo of chrome taps over undermount washroom basins" style="background:linear-gradient(160deg,#b59d7c,#3e3a45 45%,#8a8791 100%)"></div>
  <div class="card-body">
    <h3 class="heading card-title">Large Offices</h3>
    <div class="card-date"><svg width="10" height="10" viewBox="0 0 10 10"><rect y="2" width="10" height="8" fill="#333"/><rect x="2" width="1.5" height="3" fill="#333"/><rect x="6.5" width="1.5" height="3" fill="#333"/></svg>26JUL, 2016</div>
    <p class="card-text">Nemo enim ipsam voluptatem quia voluptas sit aspernatur aut odit aut fugit, sed quia conse­quuntur magni dolores eos</p>
    <span class="read-more">Read More »</span>
  </div>
</article>
<article class="abs card" style="left:775px">
  <div class="card-image" role="img" aria-label="Photo of a commercial washroom with green tiled counter and basins" style="background:linear-gradient(180deg,#e4e2d6 0%,#cfcbb8 50%,#7b8a3c 75%,#5e6b2c 100%)"></div>
  <div class="card-body">
    <h3 class="heading card-title">Large Offices</h3>
    <div class="card-date"><svg width="10" height="10" viewBox="0 0 10 10"><rect y="2" width="10" height="8" fill="#333"/><rect x="2" width="1.5" height="3" fill="#333"/><rect x="6.5" width="1.5" height="3" fill="#333"/></svg>26JUL, 2016</div>
    <p class="card-text">Nemo enim ipsam voluptatem quia voluptas sit aspernatur aut odit aut fugit, sed quia conse­quuntur magni dolores eos</p>
    <span class="read-more">Read More »</span>
  </div>
</article>

<footer class="abs footer"></footer>
<div class="abs footer-brand"><span class="brand-mark"></span><span class="brand-name">Harlow<br>Mechanical<br>Contractors</span></div>
<div class="abs social"><span></span><span></span><span></span><span></span><span></span></div>

<h4 class="abs footer-heading" style="left:406px">Quick Links</h4>
<ul class="abs quick-links"><li>Home</li><li>About Us</li><li>Services</li><li>Projects</li><li>Gallery</li><li>News</li><li>Join Us</li></ul>

<h4 class="abs footer-heading" style="left:615px">Newsletter</h4>
<p class="abs newsletter-note">Sign Up for Our Newsletter &amp; Promotion</p>
<div class="abs newsletter-input">Enter Your email Id</div>
<div class="abs subscribe">SUBSCRIBE</div>

<h4 class="abs footer-heading" style="left:884px">Contact Us</h4>
<div class="abs contact-row" style="top:2178px"><svg viewBox="0 0 12 12"><path d="M1 4c0-2 10-2 10 0v1H8V4H4v1H1zM3 6h6l2 5H1z" fill="#fff"/></svg>1800 123 4567</div>
<div class="abs contact-row" style="top:2205px"><svg viewBox="0 0 12 12"><rect x="3" y="1" width="6" height="3" fill="#fff"/><rect x="1" y="4" width="10" height="5" rx="1" fill="#fff"/><rect x="3" y="8" width="6" height="3" fill="#fff"/></svg>1800 123 4567</div>
<div class="abs contact-row" style="top:2232px"><svg viewBox="0 0 12 12"><rect x="1" y="2.5" width="10" height="7" fill="#fff"/><path d="M1 2.5l5 4 5-4" fill="none" stroke="#6e6e6e"/></svg><span style="text-decoration:underline">info@harlowmech.example</span></div>
<div class="abs contact-row" style="top:2258px;width:180px"><svg viewBox="0 0 12 12"><path d="M6 11S2 6.5 2 4.5a4 4 0 0 1 8 0C10 6.5 6 11 6 11z" fill="#fff"/><circle cx="6" cy="4.5" r="1.4" fill="#6e6e6e"/></svg><span>#2868 Lorem ipsum dolor sit amet, consectetur</span></div>

<div class="abs footer-rule"></div>
<p class="abs copyright">Copyright © 2016 Harlow Mechanical Contractors</p>

</body>
</html>
```